Business Card for my New Brokerage

Looking to get a business card design for my new Real Estate Brokerage.
I want it with Picture, Phone Number, Email, Website, Office Address
Name and Designation. Please add logo too.

Target Market(s)

Real Estate Investors or Home Buyers

Industry/Entity Type

Real Estate

Contact Information for Business Card

Name, Email, Phone Number, website, email, office address

Colors
EB3D1F
EC4F4E
F09395
F8D3D4
FCEDEE

Requirements
Must have
• Minimalistic, Clean, Modern, Photo
Nice to have
• White and Red Colors

```html
<!DOCTYPE html>
<html lang="en">
<head>
<meta charset="utf-8">
<title>Ember Realty Inc – Business Card</title>
<link href="https://fonts.googleapis.com/css2?family=Montserrat:wght@400;600;700&display=swap" rel="stylesheet">
<style>
  :root {
    --red: #e0131a;
    --red-deep: #c40c12;
    --red-light: #ec4f4e;
    --white: #ffffff;
    --backdrop: #2f3033;
    --photo-a: #e9ecef;
    --photo-b: #2b3550;
    --band: rgba(255, 255, 255, 0.12);
  }
  * { box-sizing: border-box; margin: 0; padding: 0; }
  html, body { width: 1200px; height: 896px; overflow: hidden; }
  body {
    background: var(--backdrop);
    font-family: "Montserrat", sans-serif;
    color: var(--white);
    position: relative;
  }
  .card {
    position: absolute;
    top: 298px;
    width: 520px;
    height: 300px;
    border-radius: 22px;
    overflow: hidden;
    background: linear-gradient(135deg, var(--red-light) 0%, var(--red) 45%, var(--red-deep) 100%);
  }
  .card--front { left: 50px; display: flex; align-items: center; justify-content: center; }
  .card--back { left: 630px; }

  .brand { display: flex; align-items: center; gap: 14px; }
  .brand__dot { width: 16px; height: 16px; border-radius: 50%; background: var(--white); }
  .brand__name { font-weight: 700; font-size: 40px; letter-spacing: 2px; text-transform: uppercase; }

  .photo-panel {
    position: absolute; right: 0; top: 0; width: 230px; height: 100%;
    background: var(--white);
  }
  .photo-panel__curve { position: absolute; left: 0; top: 0; width: 100%; height: 100%; }
  .photo {
    position: absolute; right: 18px; top: 36px;
    width: 228px; height: 228px; border-radius: 50%;
    background: linear-gradient(160deg, var(--photo-a) 0%, var(--photo-a) 45%, var(--photo-b) 100%);
  }

  .details { position: absolute; left: 34px; top: 30px; width: 250px; height: 240px; }
  .address { font-size: 14px; line-height: 1.45; font-weight: 400; }
  .name-band {
    position: absolute; left: -34px; top: 78px; width: 300px; padding: 10px 0 10px 34px;
    background: var(--band);
  }
  .name { font-weight: 700; font-size: 22px; letter-spacing: 1px; text-transform: uppercase; }
  .title { font-size: 14px; font-weight: 400; margin-top: 2px; }
  .contacts { position: absolute; left: 0; bottom: 0; list-style: none; font-size: 14px; line-height: 1.55; }
  .contacts li { display: flex; align-items: center; gap: 8px; }
  .contacts svg { width: 12px; height: 12px; fill: var(--white); flex: none; }
</style>
</head>
<body>
  <section class="card card--front" aria-label="Business card front">
    <div class="brand">
      <span class="brand__dot"></span>
      <span class="brand__name">Ember Realty Inc</span>
    </div>
  </section>

  <section class="card card--back" aria-label="Business card back">
    <div class="photo-panel">
      <div class="photo" role="img" aria-label="Portrait photo of the founder in a dark suit"></div>
    </div>
    <div class="details">
      <p class="address">1870 Maple Ridge Court<br>Fairview, GA 30412</p>
      <div class="name-band">
        <p class="name">Daniel Reyes</p>
        <p class="title">Founder and President</p>
      </div>
      <ul class="contacts">
        <li><svg viewBox="0 0 24 24"><path d="M6.6 10.8a15.1 15.1 0 0 0 6.6 6.6l2.2-2.2a1 1 0 0 1 1-.25 11.4 11.4 0 0 0 3.6.57 1 1 0 0 1 1 1V20a1 1 0 0 1-1 1A17 17 0 0 1 3 4a1 1 0 0 1 1-1h3.5a1 1 0 0 1 1 1c0 1.25.2 2.45.57 3.6a1 1 0 0 1-.25 1z"/></svg>+330 5510-7420</li>
        <li><svg viewBox="0 0 24 24"><path d="M2 5h20v14H2zm2 2v.5l8 5 8-5V7zm0 2.8V17h16V9.8l-8 5z"/></svg>hello@emberrealtyinc.com</li>
        <li><svg viewBox="0 0 24 24"><path d="M12 2a10 10 0 1 0 0 20 10 10 0 0 0 0-20zm6.9 9h-3a15 15 0 0 0-1.3-6 8 8 0 0 1 4.3 6zM12 4.1c.9 1.2 1.7 3.7 1.9 6.9h-3.8c.2-3.2 1-5.7 1.9-6.9zM9.4 5a15 15 0 0 0-1.3 6h-3a8 8 0 0 1 4.3-6zM5.1 13h3a15 15 0 0 0 1.3 6 8 8 0 0 1-4.3-6zm6.9 6.9c-.9-1.2-1.7-3.7-1.9-6.9h3.8c-.2 3.2-1 5.7-1.9 6.9zm2.6-.9a15 15 0 0 0 1.3-6h3a8 8 0 0 1-4.3 6z"/></svg>www.emberrealtyinc.com</li>
      </ul>
    </div>
  </section>
</body>
</html>
```